Professional and creative business card design for recruiting service providers

Our company supports German medium-sized companies in filling vacancies promptly. For this we use social media marketing and bring our customers into the visibility.

We want a professional but also creative design for our business cards.

Please look at lindqvar-staff.de to get an impression of our CI.

Target Market(s)

Small and medium-sized companies in Germany from the industry

Industry/Entity Type

Industrie, Handwerk

Contact Information for Business Card

Name, Position, Telefonnummer, Email, Website

Colors
EE7325
F08F49
F5BC92
FAE3D3
FDF4ED

Requirements
Must have
• A picture of the employee and in the style of www.lindqvar-staff.de

```html
<!DOCTYPE html>
<html lang="de">
<head>
<meta charset="utf-8">
<title>Lindqvar &amp; Staff – Visitenkarte</title>
<link rel="stylesheet" href="https://fonts.googleapis.com/css2?family=Lato:wght@400;700;900&display=swap">
<style>
  :root {
    --stage: #1b1b1b;
    --stage-glow: #2c2c2c;
    --card-dark: #141414;
    --card-light: #ffffff;
    --accent: #ee5a24;
    --ink: #161616;
    --paper-text: #ffffff;
  }
  * { margin: 0; padding: 0; box-sizing: border-box; }
  html, body {
    width: 1200px;
    height: 1015px;
    overflow: hidden;
  }
  body {
    background: radial-gradient(ellipse at 50% 45%, var(--stage-glow) 0%, var(--stage) 70%);
    font-family: "Lato", sans-serif;
    display: flex;
    flex-direction: column;
    align-items: center;
    justify-content: center;
    gap: 60px;
  }
  .card {
    width: 620px;
    height: 354px;
    position: relative;
    overflow: hidden;
    border-radius: 3px;
    box-shadow: 0 18px 40px rgba(0,0,0,.55);
  }
  /* Front side */
  .card--front {
    background: var(--card-dark);
    display: flex;
    align-items: center;
    justify-content: center;
  }
  .brand {
    display: flex;
    align-items: center;
    gap: 22px;
  }
  .brand__mark {
    width: 54px;
    height: 54px;
    background: var(--accent);
  }
  .brand__name {
    color: var(--paper-text);
    font-weight: 900;
    font-size: 34px;
    line-height: 1.08;
    letter-spacing: 4px;
    text-transform: uppercase;
  }
  /* Back side */
  .card--back { background: var(--card-light); }
  .card__art {
    position: absolute;
    inset: 0;
    width: 100%;
    height: 100%;
  }
  .identity {
    position: absolute;
    top: 38px;
    right: 34px;
    text-align: right;
  }
  .identity__name {
    color: var(--ink);
    font-weight: 700;
    font-size: 22px;
    letter-spacing: .5px;
    text-transform: uppercase;
  }
  .identity__role {
    color: var(--accent);
    font-size: 14px;
    letter-spacing: 1px;
    text-transform: uppercase;
    margin-top: 2px;
  }
  .contact {
    position: absolute;
    right: 30px;
    bottom: 50px;
    list-style: none;
    color: var(--paper-text);
    font-size: 16px;
    text-align: right;
  }
  .contact__item {
    display: flex;
    justify-content: flex-end;
    align-items: center;
    gap: 10px;
    line-height: 26px;
  }
  .contact__icon {
    width: 16px;
    height: 16px;
    flex: none;
  }
</style>
</head>
<body>

  <section class="card card--front" aria-label="Vorderseite">
    <div class="brand">
      <span class="brand__mark"></span>
      <div class="brand__name">Lindqvar<br>&amp; Staff</div>
    </div>
  </section>

  <section class="card card--back" aria-label="Rückseite">
    <svg class="card__art" viewBox="0 0 620 354" preserveAspectRatio="none">
      <defs>
        <linearGradient id="portrait-tone" x1="0" y1="0" x2="0" y2="1">
          <stop offset="0" stop-color="#c99a7e"/>
          <stop offset=".45" stop-color="#8a6552"/>
          <stop offset="1" stop-color="#1e1f26"/>
        </linearGradient>
      </defs>
      <g role="img" aria-label="Porträtfoto des Mitarbeiters">
        <rect x="140" y="60" width="230" height="260" rx="4" fill="url(#portrait-tone)"/>
      </g>
      <path d="M0,285 C170,282 260,270 340,200 C420,135 510,128 620,122 L620,354 L0,354 Z"
            fill="var(--card-light)"/>
      <path d="M0,285 C170,282 260,270 340,200 C420,135 510,128 620,122"
            fill="none" stroke="var(--accent)" stroke-width="7"/>
      <path d="M0,299 C170,296 260,284 340,214 C420,149 510,142 620,136"
            fill="none" stroke="var(--accent)" stroke-width="7"/>
      <path d="M0,313 C170,310 260,298 340,228 C420,163 510,156 620,150 L620,354 L0,354 Z"
            fill="var(--card-dark)"/>
    </svg>

    <div class="identity">
      <div class="identity__name">Markus Brenner</div>
      <div class="identity__role">Managing Director</div>
    </div>

    <ul class="contact">
      <li class="contact__item">044-987 654 321
        <svg class="contact__icon" viewBox="0 0 16 16"><path fill="var(--accent)" d="M3.5 1.5l2.5 3-1.5 1.8a9 9 0 0 0 5.2 5.2l1.8-1.5 3 2.5-1.6 2A12 12 0 0 1 1.5 3.1z"/></svg>
      </li>
      <li class="contact__item">info@lindqvar-staff.de
        <svg class="contact__icon" viewBox="0 0 16 16"><rect x="1" y="3" width="14" height="10" fill="var(--accent)"/><path d="M1 3l7 6 7-6" fill="none" stroke="var(--card-dark)" stroke-width="1.3"/></svg>
      </li>
      <li class="contact__item">www.lindqvar-staff.de
        <svg class="contact__icon" viewBox="0 0 16 16"><circle cx="8" cy="8" r="7" fill="var(--accent)"/><g fill="none" stroke="var(--card-dark)" stroke-width="1"><ellipse cx="8" cy="8" rx="3" ry="7"/><path d="M1 8h14M2.2 4.5h11.6M2.2 11.5h11.6"/></g></svg>
      </li>
    </ul>
  </section>

</body>
</html>
```